Tall ridge firewood

It a new firewood outlet in Jindabyne nsw that will only sell top hardwood firewood (ironbark , red gum, grey gum, an box mix. I would like to see a web page the we can do order online payment for delivery. It will all so need to have photos of the firewood. I all so have logo for tall ridge firewood
Must have a modem look but easy to use I would like to see a black back ground of some sort.

Here are some other firewood web pages for ideas and firewood info
http://www.example-logpile.com.au
http://www.example-stackwood.com.au
http://www.example-splitlog.com.au
http://www.example-kendaltimber.com.au/firewood

Industry/Entity Type

Firewood

```html
<!DOCTYPE html>
<html lang="en">
<head>
<meta charset="utf-8">
<title>Tall Ridge Firewood</title>
<link href="https://fonts.googleapis.com/css2?family=Anton&family=Noto+Sans:wght@400;700&display=swap" rel="stylesheet">
<style>
:root{
  --ink:#111;
  --dark:#1c1c1c;
  --panel:#3a3a3a;
  --blue:#1f72bb;
  --blue-dark:#1a5f9c;
  --white:#fff;
  --muted:#d6d6d6;
  --rule:#555;
}
*{box-sizing:border-box;margin:0;padding:0}
html,body{width:1093px;height:1200px;overflow:hidden}
body{position:relative;background:var(--white);font-family:"Noto Sans",Verdana,sans-serif;color:var(--white)}
.abs{position:absolute}
.display{font-family:"Anton",Impact,sans-serif;font-weight:400}
a{color:inherit}

/* header */
.topbar{left:0;top:0;width:1093px;height:92px;background:linear-gradient(90deg,#0c0c0c,#202020 30%,#111 60%,#1d1d1d)}
.contact-line{left:146px;font-size:10px;display:flex;align-items:center;gap:6px}
.contact-line.phone{top:22px}
.contact-line.email{top:45px}
.contact-line .big{font-family:"Anton",Impact,sans-serif;font-size:17px;letter-spacing:.3px}
.contact-line .mail{text-decoration:underline;color:var(--muted)}
.search{left:498px;top:28px;width:221px;height:26px;border:1px solid #777;border-radius:3px;background:#222;display:flex}
.search span{flex:1;font-size:10px;color:#bbb;padding:6px 8px}
.search .go{width:26px;background:var(--blue);border-radius:0 2px 2px 0;display:flex;align-items:center;justify-content:center}
.cart{left:826px;top:21px;width:120px;font-size:10px;display:flex;align-items:center;justify-content:flex-end;gap:5px}
.cart .big{font-family:"Anton",Impact,sans-serif;font-size:12px}
.order-btn{left:851px;top:42px;width:95px;height:22px;border-radius:3px;background:linear-gradient(#fff,#d9d9d9);color:#111;font-size:10px;text-align:center;line-height:22px}

/* navigation */
.mainnav{left:0;top:92px;width:1093px;height:32px;background:var(--blue)}
.mainnav ul{list-style:none;position:absolute;left:146px;top:0;display:flex;height:32px}
.mainnav li{font-size:10px;line-height:32px;text-align:center;border-right:1px solid #1a5c98}
.mainnav li.active{background:#2f2f2f}

/* hero */
.brand{left:146px;top:200px;width:260px;height:200px;display:flex;flex-direction:column;align-items:center;justify-content:center;gap:6px;color:var(--blue)}
.brand .mark{width:18px;height:18px;border-radius:50%;background:var(--blue)}
.brand .name{font-size:22px;font-weight:700;letter-spacing:.5px}
.brand .tag{font-size:8px;color:#222;letter-spacing:1px}
.hero-photo{left:451px;top:137px;width:495px;height:325px;border:3px solid #333;background:radial-gradient(circle at 40% 45%,#c08d5c,#8b6239 60%,#5a3c22)}

/* dark content */
.woodband{left:0;top:474px;width:1093px;height:531px;background:linear-gradient(90deg,#0d0d0d,#1e1e1e 20%,#121212 45%,#1b1b1b 70%,#0e0e0e)}
.h-section{font-size:24px;line-height:1}
.welcome-title{left:146px;top:502px}
.body-copy{left:146px;top:543px;width:480px;font-size:10px;line-height:12.5px;color:#e8e8e8}
.body-copy p+p{margin-top:12px}
.vrule{left:669px;top:504px;width:1px;height:192px;background:var(--rule)}
.why-title{left:721px;top:502px}
.reasons{left:718px;top:543px;width:230px;list-style:none}
.reasons li{display:flex;gap:14px;font-size:10px;line-height:13px;color:#e8e8e8;margin-bottom:14px}
.reasons .tick{flex:none;width:18px;height:18px;border-radius:4px;background:#444;display:flex;align-items:center;justify-content:center}
.btn-blue{left:722px;top:674px;width:79px;height:22px;border-radius:3px;background:var(--blue);font-size:10px;text-align:center;line-height:22px}
.products-title{left:163px;top:728px}
.view-all{left:885px;top:736px;font-size:10px;text-decoration:underline}
.hrule{left:146px;top:767px;width:800px;height:1px;background:var(--rule)}
.arrow{top:825px}
.product{top:795px;width:163px;text-align:center}
.product .thumb{width:163px;height:116px;border:3px solid #cfcfcf}
.product .name{margin-top:16px;font-size:14px}
.product .price{margin-top:4px;font-size:14px;color:var(--blue)}

/* footer */
.footer{left:0;top:1005px;width:1093px;height:163px;background:var(--panel)}
.fcol-title{font-size:10px;font-weight:700;top:1026px}
.flist{list-style:none;top:1047px;font-size:9.5px;line-height:14.4px}
.flist li::before{content:"»";margin-right:6px}
.frule{top:1028px;width:1px;height:118px;background:#555}
.socials{left:468px;top:1050px;display:flex;gap:5px}
.socials span{width:24px;height:24px;background:var(--blue)}
.client-title{left:656px;top:1022px;font-size:15px;font-weight:700}
.client-copy{left:656px;top:1046px;width:270px;font-size:9.5px;line-height:12.5px;color:#ddd}
.client-sign{left:656px;top:1097px;font-size:9.5px;color:#ddd}
.btn-light{left:657px;top:1127px;width:80px;height:22px;border-radius:3px;background:linear-gradient(#fff,#d6d6d6);color:#111;font-size:10px;text-align:center;line-height:22px}
.copyright{left:0;top:1168px;width:1093px;height:32px;background:var(--blue);font-size:9.5px;text-align:center;line-height:32px}
</style>
</head>
<body>

<header class="abs topbar"></header>
<div class="abs contact-line phone">
  <svg width="12" height="14" viewBox="0 0 12 14"><path d="M2 1 L5 1 L6 4 L4 5 Q5 8 8 10 L9 8 L12 9 L12 12 Q9 14 5 10 Q1 6 2 1Z" fill="#bbb"/></svg>
  <span>CALL US -</span><span class="big">5550 218 604</span>
</div>
<div class="abs contact-line email">
  <svg width="12" height="9" viewBox="0 0 12 9"><rect x=".5" y=".5" width="11" height="8" fill="none" stroke="#bbb"/><path d="M.5 .5 L6 5 L11.5 .5" fill="none" stroke="#bbb"/></svg>
  <span>EMAIL US -</span><span class="mail">INFO@TALLRIDGEFIREWOOD.EXAMPLE</span>
</div>
<div class="abs search"><span>Find Firewood Products ..</span>
  <div class="go"><svg width="13" height="13" viewBox="0 0 13 13"><circle cx="5.5" cy="5.5" r="4" fill="none" stroke="#fff" stroke-width="2"/><path d="M8.5 8.5 L12 12" stroke="#fff" stroke-width="2"/></svg></div>
</div>
<div class="abs cart">
  <svg width="12" height="10" viewBox="0 0 12 10"><path d="M0 1 H2 L4 7 H10 L11 3 H3" fill="none" stroke="#ccc"/><circle cx="5" cy="9" r="1" fill="#ccc"/><circle cx="9" cy="9" r="1" fill="#ccc"/></svg>
  <span>MY CART -</span><span class="big">0 ITEM (S)</span>
</div>
<div class="abs order-btn">ORDER ONLINE</div>

<nav class="abs mainnav">
  <ul>
    <li class="active" style="width:100px">HOME</li>
    <li style="width:112px">ABOUT US</li>
    <li style="width:118px">PRODUCTS</li>
    <li style="width:129px">ACCESSORIES</li>
    <li style="width:113px">DELIVERY</li>
    <li style="width:98px">FAQ`S</li>
    <li style="width:130px;border-right:0">CONTACT US</li>
  </ul>
</nav>

<div class="abs brand">
  <span class="mark"></span>
  <span class="name">TALL RIDGE FIREWOOD</span>
  <span class="tag">WOOD THAT KEEPS YOU WARM ALL NIGHT LONG · 0400 555 019</span>
</div>
<div class="abs hero-photo" role="img" aria-label="Photo of a pile of cut hardwood log rounds"></div>

<section class="abs woodband"></section>
<h1 class="abs display h-section welcome-title">Welcome to Tall Ridge Firewood</h1>
<div class="abs body-copy">
  <p>Lorem ipsum dolor sit amet, consectetur adipisicing elit, sed do eiusmod tempor incididunt ut labore et dolore magna aliqua. Ut enim ad minim veniam, quis nostrud exercitation ullamco laboris nisi ut aliquip ex ea commodo consequat. Duis aute irure dolor in reprehenderit in voluptate velit esse cillum dolore eu fugiat nulla pariatur. Excepteur sint occaecat cupidatat non proident, sunt in culpa qui officia deserunt mollit anim id est laborum.</p>
  <p>Lorem ipsum dolor sit amet, consectetur adipisicing elit, sed do eiusmod tempor incididunt ut labore et dolore magna aliqua. Ut enim ad minim veniam, quis nostrud exercitation ullamco laboris nisi ut aliquip ex ea commodo consequat. Duis aute irure dolor in reprehenderit in voluptate velit esse cillum dolore eu fugiat nulla pariatur. Excepteur sint occaecat cupidatat non proident, sunt in culpa qui officia deserunt mollit anim id est laborum.</p>
</div>
<div class="abs vrule"></div>
<h2 class="abs display h-section why-title">Why Choose Us ?</h2>
<ul class="abs reasons">
  <li><span class="tick"><svg width="10" height="8" viewBox="0 0 10 8"><path d="M1 4 L4 7 L9 1" fill="none" stroke="#aaa" stroke-width="2"/></svg></span>Lorem ipsum dolor sit amet, consectetur adipisicing elit.</li>
  <li><span class="tick"><svg width="10" height="8" viewBox="0 0 10 8"><path d="M1 4 L4 7 L9 1" fill="none" stroke="#aaa" stroke-width="2"/></svg></span>Lorem ipsum dolor sit amet, consectetur adipisicing elit, sed do eiusmod tempor.</li>
  <li><span class="tick"><svg width="10" height="8" viewBox="0 0 10 8"><path d="M1 4 L4 7 L9 1" fill="none" stroke="#aaa" stroke-width="2"/></svg></span>Lorem ipsum dolor sit amet, consectetur adipisicing elit, sed do.</li>
</ul>
<div class="abs btn-blue">READ MORE</div>

<h2 class="abs display h-section products-title">Top Hardwood Firewood Products</h2>
<div class="abs view-all">VIEW ALL</div>
<div class="abs hrule"></div>
<svg class="abs arrow" style="left:146px" width="12" height="57" viewBox="0 0 12 57"><path d="M11 1 L1 28 L11 56" fill="none" stroke="#ddd" stroke-width="1.5"/></svg>
<svg class="abs arrow" style="left:936px" width="12" height="57" viewBox="0 0 12 57"><path d="M1 1 L11 28 L1 56" fill="none" stroke="#ddd" stroke-width="1.5"/></svg>

<div class="abs product" style="left:181px">
  <div class="thumb" role="img" aria-label="Photo of split ironbark firewood in a trailer" style="background:linear-gradient(#8a5a4a,#a0705f 55%,#666 80%,#555)"></div>
  <div class="name">Ironbark</div><div class="price display">$30.20 Only</div>
</div>
<div class="abs product" style="left:370px">
  <div class="thumb" role="img" aria-label="Photo of split red gum firewood being handled" style="background:linear-gradient(120deg,#6e2a1c,#a23a28 50%,#5b2a1e)"></div>
  <div class="name">Red Gum</div><div class="price display">$30.20 Only</div>
</div>
<div class="abs product" style="left:561px">
  <div class="thumb" role="img" aria-label="Photo of a pile of grey gum log rounds" style="background:linear-gradient(135deg,#7c7f88,#a5a6ab 50%,#6a6d73)"></div>
  <div class="name">Grey Gum</div><div class="price display">$30.20 Only</div>
</div>
<div class="abs product" style="left:750px">
  <div class="thumb" role="img" aria-label="Photo of a box mix of firewood burning in a fireplace" style="background:radial-gradient(ellipse at 50% 60%,#e0562a,#7a2312 35%,#1a1a1a 65%)"></div>
  <div class="name">Box Mix</div><div class="price display">$30.20 Only</div>
</div>

<footer class="abs footer"></footer>
<div class="abs fcol-title" style="left:180px">NAVIGATION</div>
<ul class="abs flist" style="left:180px">
  <li>Home</li><li>About Us</li><li>Products</li><li>Accessories</li><li>Delivery</li><li>Faq`s</li><li>Contact Us</li>
</ul>
<div class="abs frule" style="left:295px"></div>
<div class="abs fcol-title" style="left:337px">PRODUCTS</div>
<ul class="abs flist" style="left:337px">
  <li>Ironbark</li><li>Red gum</li><li>Grey gum</li><li>Box mix</li>
</ul>
<div class="abs frule" style="left:433px"></div>
<div class="abs fcol-title" style="left:468px">FOLLOW US ON</div>
<div class="abs socials">
  <span role="img" aria-label="Social network link"></span>
  <span role="img" aria-label="Social network link"></span>
  <span role="img" aria-label="Social network link"></span>
  <span role="img" aria-label="Social network link"></span>
</div>
<div class="abs frule" style="left:619px"></div>
<div class="abs client-title">Happy Client`s</div>
<p class="abs client-copy">Lorem ipsum dolor sit amet, consectetur adipisicing elit, sed do eiusmod tempor incididunt ut labore et dolore magna aliqua.</p>
<div class="abs client-sign"><b>Sam</b>. 15/06/13</div>
<div class="abs btn-light">READ MORE</div>

<div class="abs copyright">COPYRIGHT © <b>TALL RIDGE FIREWOOD</b> 2013. ALL RIGHT RESERVED.</div>

</body>
</html>
```